Mortgage Company ready to make a statement!

We have a basic logo that I am fairly happy with ... but it could use a little bit of tweaking before we order the sign for our building. We also want some knock-your-socks-off business cards.
Problem: Inside of our Mortgage Office (Bright Fern Mortgage Group), we are going to have a coffee lounge (Sunbrew Cafe) for Realtors to use instead of the local Cuppington to meet with homebuyers. The office and coffee lounge are in an industrial building and is decorated with cozy overstuffed chairs, a hodge podge of interesting lamps and furniture, and goal is to make it as inviting as possible. However, we are a financial institution... so we need to keep it pretty clean as well.
One of my favorite marketing ideas is to cut a house key for everyone who buys a home using us with a key that matches our logo. There's only one key shape that works really well, so that needs to match the logo in order for the idea to work. I'll attach an image of the key blank.... although the way the key hole cut out looks terrible, so I was thinking of having them just do a thin outline instead.
Would like a similar, matching logo for the Sunbrew Cafe... but possibly something that would be a little less formal and would be cute on a coffee mug- nothing stuffy.
AND, we're opening a home inspection company as well, and we would like that logo and branding to match. The home inspection company is "Bright Fern Home Inspections"
We were thinking that for the home inspection company , we could use a magnifying glass shape inside of the house shape for the logo, use a keyhole shape inside of the same house for the mortgage company, and use a coffee cup inside of the house shape for Sunbrew Cafe.
Just getting stuck and need to help. I designed the attached logo myself, and that is what we are currently using. Designers at local printing companies have failed to impress us.
The mortgage industry has a lot of numbers and logos, etc that they require us to put on our business cards... so it's hard to keep them looking clean.
HELP! HELP! :)

```html
<!DOCTYPE html>
<html lang="en">
<head>
<meta charset="utf-8">
<title>Bright Fern Mortgage Group – Business Cards</title>
<link href="https://fonts.googleapis.com/css2?family=Marcellus&family=Montserrat:wght@400;500;700&display=swap" rel="stylesheet">
<style>
  :root {
    --backdrop: #e9eaec;
    --card: #ffffff;
    --teal: #1f5f82;
    --ink: #45444f;
    --text: #3c3c44;
  }
  * { box-sizing: border-box; margin: 0; padding: 0; }
  html, body {
    width: 1200px; height: 900px; overflow: hidden;
    background: var(--backdrop);
  }
  .canvas { position: relative; width: 1200px; height: 900px; }
  .card {
    position: absolute; left: 250px; width: 700px; height: 400px;
    background: var(--card);
    box-shadow: 0 6px 18px rgba(0,0,0,0.12);
    overflow: hidden;
  }
  .card--front { top: 40px; }
  .card--back { top: 470px; }

  /* Front */
  .brand {
    position: absolute; left: 100px; top: 118px;
    display: flex; align-items: center; gap: 30px;
  }
  .brand__mark {
    width: 96px; height: 96px; border-radius: 50%;
    background: var(--teal); flex: none;
  }
  .brand__name {
    font-family: "Marcellus", serif; font-weight: 400;
    color: var(--teal); font-size: 50px; line-height: 1.08;
    letter-spacing: 1px; white-space: nowrap;
  }

  /* Back */
  .back-brand {
    position: absolute; left: 44px; top: 0; bottom: 0; width: 290px;
    display: flex; flex-direction: column; justify-content: center; gap: 18px;
  }
  .back-brand__mark {
    width: 120px; height: 120px; border-radius: 50%;
    background: var(--teal);
  }
  .back-brand__name {
    font-family: "Marcellus", serif; font-weight: 400;
    color: var(--teal); font-size: 30px; line-height: 1.12; white-space: nowrap;
  }
  .divider {
    position: absolute; left: 352px; top: 100px; width: 2px; height: 200px;
    background: var(--teal);
  }
  .contact {
    position: absolute; left: 378px; top: 104px;
    font-family: "Montserrat", sans-serif; color: var(--text);
  }
  .contact__name {
    font-family: "Marcellus", serif; font-weight: 400; color: var(--teal);
    font-size: 28px; letter-spacing: 1.5px; line-height: 1;
  }
  .contact__role {
    font-weight: 700; font-size: 17px; letter-spacing: 1px;
    color: var(--ink); margin-top: 4px;
  }
  .contact__address {
    margin-top: 18px; font-size: 15px; line-height: 1.35; letter-spacing: 1px;
  }
  .contact__list { list-style: none; margin-top: 12px; }
  .contact__item {
    display: flex; align-items: center; gap: 12px;
    font-size: 15px; letter-spacing: 0.6px; line-height: 1.6; white-space: nowrap;
  }
  .icon { width: 14px; height: 14px; fill: var(--teal); flex: none; }
</style>
</head>
<body>
<main class="canvas">

  <section class="card card--front" aria-label="Card front">
    <div class="brand">
      <span class="brand__mark"></span>
      <div class="brand__name">Bright Fern<br>Mortgage Group</div>
    </div>
  </section>

  <section class="card card--back" aria-label="Card back">
    <div class="back-brand">
      <span class="back-brand__mark"></span>
      <div class="back-brand__name">Bright Fern<br>Mortgage Group</div>
    </div>
    <div class="divider"></div>
    <div class="contact">
      <h1 class="contact__name">DANIEL MARSH</h1>
      <p class="contact__role">CEO</p>
      <p class="contact__address">Harbour Point<br>Brisbane</p>
      <ul class="contact__list">
        <li class="contact__item">
          <svg class="icon" viewBox="0 0 14 14" aria-hidden="true"><path d="M4 0h6a1 1 0 0 1 1 1v12a1 1 0 0 1-1 1H4a1 1 0 0 1-1-1V1a1 1 0 0 1 1-1zm0.5 1.5v9h5v-9zM7 11.3a.8.8 0 1 0 0 1.6.8.8 0 0 0 0-1.6z"/></svg>
          000-555-0142
        </li>
        <li class="contact__item">
          <svg class="icon" viewBox="0 0 14 14" aria-hidden="true"><path d="M3 0h8v4H3zM1 5h12a1 1 0 0 1 1 1v5h-3v3H3v-3H0V6a1 1 0 0 1 1-1zm3 5v3h6v-3z"/></svg>
          000-555-0142
        </li>
        <li class="contact__item">
          <svg class="icon" viewBox="0 0 14 14" aria-hidden="true"><path d="M0 2h14v1.2L7 8 0 3.2zM0 4.6l7 4.8 7-4.8V12H0z"/></svg>
          daniel.marsh@brightfernmg.com
        </li>
      </ul>
    </div>
  </section>

</main>
</body>
</html>
```